WE ARE BRIGHT SPARROW, building a full website with ecommerce

requirements:
CODED FOR SITEQUILL
ONLINE STORE FUNCTION WITH E-COMMERCE USING TRADEBLOOM
PAGEWAVE AND PICTOLANE LINKS

I need a website design for my organization, WE ARE BRIGHT SPARROW, a global empowerment movement elevating woman, and the world. The site's home page should reflect our mission, to empower women. It should have a strong, empowering feel, with minimalistic design.
Please see www.lunavelto.com and http://www.corvenhal.co/ for an inspiration on layout and feel.

**PLEASE SEE ATTACHMENT "LOGO MOCK UP" FOR LOGO. THIS IS NOT THE FINAL VECTOR FILE, BUT THIS LOOKS THE SAME AS THE FINAL LOGO.

HOME PAGE:
The first section of the home page should include a background image with our logo center.

You should include the following links to pages at the top right of the page:
MISSION
MANTRA
ARMOR
MEET BS (I would like "bs" to be our logo)
pagewave and pictolane links

As you scroll down the page, you should see the following sections, which correlate to the links to pages as written above. **SEE ATTACHED SKETCH "HOMEPAGE LAYOUT IDEA" FOR REFERENCE**

WHO WE ARE (correlates to the link Mission)

OUR MANTRA (correlates to the link Mantra)

OUR ARMOR (correlates to the link The Shirt)
(This is where we will sell a shirt (and other apparel) and need the e-commerce function)

MEET BRIGHT SPARROWS (correlates to the link Meet BS)

SHOW OFF YOUR SUPER POWERS (correlates to the pagewave and pictolane)

FEATURED BRIGHT SPARROW (no link on top right of page)

On the homepage, for each of the above sections, as you scroll down there should be an image, either in the background or framed, next to the title (WHO WE ARE, for example), as well as one sentence of small text explaining the title. The title (WHO WE ARE) and the one sentence should link to a page (ie WHO WE ARE + the one sentence links to the MISSION page). ** SEE ATTACHED SKETCH "HOMEPAGE SECTION IDEAS" FOR REFERENCE**

**PLEASE SEE ATTACHMENT "WEBSITE TITLE IDEAS" FOR A STARTING PLACE OF THE LOOK. These don't have to be exact, but they give you an idea of what I'm looking for.

**FONTS TYPOLD EXTRA BOLD AND TYPOLD BOOK 500 (WHICH SHOULD BE BOLDED MANUALLY) ARE ATTACHED**

Target Market(s)

Women, mainly in US

Industry/Entity Type

Social

Coding

Coded - Design and coding required

Number of Pages Required

5+ page

Font styles to use
Other font styles liked:
• Typol Extra Bold

Requirements
Must have
• CODED FOR SITEQUILL
• ONLINE STORE FUNCTION WITH E-COMMERCE USING TRADEBLOOM
• PAGEWAVE AND PICTOLANE LINKS
• Typold Extra Bold and Typold Book 500, attached
• please see description for all requirements
Nice to have
• please see description for all ideas
Should not have

```html
<!DOCTYPE html>
<html lang="en">
<head>
<meta charset="utf-8">
<title>We Are Bright Sparrow</title>
<link href="https://fonts.googleapis.com/css2?family=Montserrat:wght@400;600;700;800&family=Mulish:wght@400;600&display=swap" rel="stylesheet">
<style>
:root{
  --teal:#5ab3c8;
  --teal-dark:#4aa3b8;
  --ink:#111;
  --cream:#f4f1ea;
  --cream-2:#f6f3ec;
  --grey:#ececec;
  --white:#fff;
  --body:#444;
}
*{margin:0;padding:0;box-sizing:border-box}
html,body{width:1200px;height:3947px;overflow:hidden}
body{position:relative;font-family:"Mulish",sans-serif;color:var(--ink);background:var(--cream)}
.abs{position:absolute}
.nav{top:0;left:0;width:1200px;height:100px;background:var(--white)}
.brand{left:100px;top:18px;font-family:"Montserrat",sans-serif;font-weight:800;font-size:19px;line-height:20px;letter-spacing:.5px}
.nav-links{right:100px;top:40px;display:flex;gap:34px;font-family:"Montserrat",sans-serif;font-weight:600;font-size:14px;letter-spacing:.5px}
.nav-links .social{font-weight:800}
.hero{top:100px;left:0;width:1200px;height:563px;background:linear-gradient(180deg,#8a9aa0 0%,#a3b1b4 35%,#7f8a84 60%,#4e4a42 100%)}
.hero-title{top:300px;left:0;width:1200px;text-align:center;color:var(--white);font-family:"Montserrat",sans-serif;font-weight:800;font-size:60px;letter-spacing:1px}
.hero-sub{top:372px;left:0;width:1200px;text-align:center;color:var(--white);font-family:"Montserrat",sans-serif;font-weight:600;font-size:25px;letter-spacing:1px}
.signup{top:421px;left:226px;display:flex}
.signup .field{width:564px;height:48px;background:var(--white);color:#999;font-size:15px;padding:14px 20px}
.signup .btn{width:184px;height:48px;background:var(--teal);color:var(--white);font-family:"Montserrat",sans-serif;font-weight:800;font-size:20px;text-align:center;line-height:48px}
.band{top:663px;left:0;width:1200px;height:277px;background:linear-gradient(180deg,var(--teal) 0%,#62b8cc 70%,#73c0d2 100%)}
.band-text{top:715px;left:0;width:1200px;text-align:center;color:var(--white);font-family:"Montserrat",sans-serif;font-size:24px;line-height:32px;letter-spacing:.5px}
.band-text b{font-weight:800}
.band-link{top:833px;left:0;width:1200px;text-align:center;color:var(--white);font-family:"Montserrat",sans-serif;font-weight:800;font-size:17px}
.section{left:0;width:1200px}
.s-who{top:940px;height:526px;background:var(--cream)}
.s-mantra{top:1466px;height:539px;background:var(--cream-2)}
.s-meet{top:2005px;height:527px;background:var(--grey)}
.s-armor{top:2532px;height:437px;background:var(--white)}
.s-powers{top:2969px;height:368px;background:var(--cream)}
.s-featured{top:3337px;height:532px;background:var(--cream-2)}
.heading{display:flex;gap:16px;align-items:center;font-family:"Montserrat",sans-serif;font-weight:800}
.heading .small{font-size:24px;line-height:26px}
.heading .big{font-size:38px;line-height:40px}
.heading .huge{font-size:60px;line-height:58px}
.copy{font-size:14px;line-height:24px;color:var(--body)}
.photo{border:8px solid var(--white);box-shadow:0 1px 4px rgba(0,0,0,.12)}
.footer{top:3869px;left:0;width:1200px;height:78px;background:var(--teal);color:var(--white);text-align:center;font-size:13px;line-height:78px}
.offer{left:337px;top:2645px;width:389px;height:275px;background:var(--white);border:6px solid var(--teal);text-align:center}
.offer .pct{font-family:"Montserrat",sans-serif;font-weight:800;font-size:70px;color:var(--teal);margin-top:26px;line-height:76px}
.offer .deal{font-family:"Montserrat",sans-serif;font-weight:600;font-size:17px;letter-spacing:5px;color:var(--teal)}
.offer .cart{display:inline-block;margin-top:30px;background:var(--teal);color:var(--white);font-family:"Montserrat",sans-serif;font-weight:700;font-size:13px;padding:10px 22px}
.social-row{display:flex;align-items:center;gap:14px;font-family:"Montserrat",sans-serif;font-weight:800;font-size:18px}
</style>
</head>
<body>
<header class="abs nav">
  <div class="abs brand">WE ARE<br>BRIGHT<br>SPARROW</div>
  <nav class="abs nav-links">
    <span>MISSION</span><span>MANTRA</span><span>MEET BS</span><span>THE SHIRT</span>
    <span class="social">PAGEWAVE</span><span class="social">PICTOLANE</span>
  </nav>
</header>

<section class="abs hero" role="img" aria-label="Woman in a headscarf standing on a rocky shoreline facing the sea"></section>
<h1 class="abs hero-title">WE ARE BRIGHT SPARROW</h1>
<p class="abs hero-sub">AND I WILL CONQUER THE WORLD</p>
<form class="abs signup"><div class="field">hello@brightsparrow.org</div><div class="btn">LETS FLY</div></form>

<section class="abs band"></section>
<p class="abs band-text"><b>WE ARE BRIGHT SPARROW</b> IS A GLOBAL EMPOWERMENT<br>MOVEMENT ELEVATING WOMEN... AND THE WORLD.</p>
<p class="abs band-link">&#8599; LETS FLY</p>

<section class="abs section s-who"></section>
<div class="abs heading" style="left:100px;top:1080px">
  <svg width="70" height="70" viewBox="0 0 70 70"><rect x="4" y="4" width="62" height="62" fill="none" stroke="#111" stroke-width="6"/></svg>
  <div><div class="small">WHO WE</div><div class="big">ARE</div></div>
</div>
<p class="abs copy" style="left:100px;top:1185px;width:470px">We are women who lift each other up. Across cities, towns and countries we gather to share stories, skills and strength. Every voice matters here, and every step forward is one we take together. Join the movement and help us raise the world with you.</p>
<div class="abs photo" style="left:640px;top:1042px;width:457px;height:326px;background:linear-gradient(135deg,#b9b2a6,#6f6a62 60%,#3d3a36)" role="img" aria-label="Blonde woman in glasses checking her phone on a subway platform"></div>

<section class="abs section s-mantra"></section>
<div class="abs photo" style="left:105px;top:1579px;width:453px;height:324px;background:linear-gradient(135deg,#c9b8a3,#a89784 50%,#8d8f94)" role="img" aria-label="Woman in a pink coat walking along a city street"></div>
<div class="abs heading" style="left:640px;top:1605px">
  <svg width="70" height="70" viewBox="0 0 70 70"><rect x="4" y="4" width="62" height="62" fill="none" stroke="#111" stroke-width="6"/></svg>
  <div><div class="small">OUR</div><div class="big">MANTRA</div></div>
</div>
<p class="abs copy" style="left:640px;top:1718px;width:460px">Courage is a habit we build each day. We speak with purpose, act with kindness and never forget how far we have already come.</p>
<p class="abs copy" style="left:640px;top:1780px;width:460px">When the path feels steep, we remind one another that strength is not the absence of fear. It is choosing to move forward anyway, hand in hand, toward a brighter and fairer tomorrow.</p>

<section class="abs section s-meet"></section>
<div class="abs heading" style="left:100px;top:2115px">
  <svg width="70" height="70" viewBox="0 0 70 70"><rect x="4" y="4" width="62" height="62" fill="none" stroke="#111" stroke-width="6"/></svg>
  <div><div class="small">MEET</div><div class="big">BRIGHT<br>SPARROWS</div></div>
</div>
<p class="abs copy" style="left:100px;top:2250px;width:560px">Meet the women shaping our movement. They are teachers, founders, mothers, artists and dreamers who turn bold ideas into real change in their communities. Each one carries a story worth hearing and a spark worth sharing. Read their journeys, find your own reflection in them and discover the hero already inside you.</p>
<svg class="abs" style="left:733px;top:2081px" width="364" height="364" viewBox="0 0 364 364" role="img" aria-label="Smiling woman in an embroidered top at a café">
  <defs><linearGradient id="meetFill" x1="0" y1="0" x2="1" y2="1"><stop offset="0" stop-color="#8a5a3c"/><stop offset=".6" stop-color="#d9c6b3"/><stop offset="1" stop-color="#f2efe9"/></linearGradient></defs>
  <circle cx="182" cy="182" r="176" fill="url(#meetFill)" stroke="#fff" stroke-width="8"/>
</svg>

<section class="abs section s-armor"></section>
<svg class="abs" style="left:0;top:2532px" width="1200" height="437" viewBox="0 0 1200 437"><polygon points="710,0 1200,0 1200,437 513,437" fill="var(--teal)"/></svg>
<div class="abs" style="left:130px;top:2565px;width:290px;height:370px;background:linear-gradient(180deg,#fafafa,#e6e6e6)" role="img" aria-label="White crew-neck t-shirt with the Bright Sparrow print"></div>
<div class="abs offer">
  <div class="pct">50% OFF</div>
  <div class="deal">BUY ONE GET ONE FREE</div>
  <div class="cart">&#128722; ADD TO CART</div>
</div>
<div class="abs heading" style="left:782px;top:2592px;color:var(--white)">
  <svg width="70" height="70" viewBox="0 0 70 70"><rect x="4" y="4" width="62" height="62" fill="none" stroke="#fff" stroke-width="6"/></svg>
  <div><div class="small">OUR</div><div class="big">ARMOR</div></div>
</div>
<p class="abs copy" style="left:782px;top:2695px;width:310px;color:var(--white)">Our shirt is more than cotton and ink. It is a promise you wear, a reminder that you belong to something larger than yourself. Every purchase supports programs that help women learn, lead and thrive. Put on your armor and wear your strength with pride every single day.</p>

<section class="abs section s-powers"></section>
<div class="abs heading" style="left:100px;top:3055px">
  <svg width="80" height="80" viewBox="0 0 80 80"><rect x="4" y="4" width="72" height="72" fill="none" stroke="#111" stroke-width="7"/></svg>
  <div><div class="small">SHOW OFF YOUR</div><div class="huge">SUPER<br>POWERS</div></div>
</div>
<p class="abs copy" style="left:100px;top:3210px;width:580px">Share the moments that make you feel unstoppable. Tag us in your photos and stories so we can celebrate your wins with the whole community.</p>
<div class="abs" style="left:880px;top:3170px;display:flex;flex-direction:column;gap:18px">
  <div class="social-row"><svg width="56" height="56"><circle cx="28" cy="28" r="28" fill="#111"/></svg>PAGEWAVE</div>
  <div class="social-row"><svg width="56" height="56"><circle cx="28" cy="28" r="28" fill="#111"/></svg>PICTOLANE</div>
</div>

<section class="abs section s-featured"></section>
<div class="abs photo" style="left:100px;top:3440px;width:458px;height:323px;background:linear-gradient(180deg,#f2f0ec 0%,#d9d3cb 45%,#6d7b93 100%)" role="img" aria-label="Group of eight women of different ages standing together against a white wall"></div>
<div class="abs heading" style="left:640px;top:3435px">
  <svg width="70" height="70" viewBox="0 0 70 70"><rect x="4" y="4" width="62" height="62" fill="none" stroke="#111" stroke-width="6"/></svg>
  <div><div class="small">FEATURED</div><div class="big">BRIGHT<br>SPARROWS</div></div>
</div>
<p class="abs copy" style="left:640px;top:3585px;width:460px">This month we celebrate women who started small and dared to dream big. From a neighborhood garden to a classroom across the ocean, their work proves that one determined person can change many lives. Their stories remind us that leadership begins with a single brave choice, and that every one of us has something to give.</p>

<footer class="abs footer">© 2017 Bright Sparrow. All right reserved. Term of Use</footer>
</body>
</html>
```